TALMORK

The business want a professional looking business card. We have a scetch we will add but want the extra upgrade, and would like more suggestions for variations of our business cards.

```html
<!DOCTYPE html>
<html lang="en">
<head>
<meta charset="utf-8">
<title>TALMORK business card</title>
<link rel="stylesheet" href="https://fonts.googleapis.com/css2?family=Arimo:wght@400&display=swap">
<style>
  :root {
    --backdrop: #3d3d3d;
    --card: #ffffff;
    --gold: #b8914a;
    --ink: #555555;
    --rule: #d9d4cc;
  }
  html, body {
    margin: 0;
    padding: 0;
    width: 1200px;
    height: 1200px;
    overflow: hidden;
    background: var(--backdrop);
    font-family: "Arimo", Arial, sans-serif;
  }
  .canvas {
    position: relative;
    width: 1200px;
    height: 1200px;
  }
  .card {
    position: absolute;
    width: 688px;
    height: 393px;
    background: var(--card);
    border-radius: 26px;
  }
  .card--front { left: 267px; top: 158px; }
  .card--back  { left: 263px; top: 653px; }

  .brand {
    position: absolute;
    text-align: center;
    color: var(--gold);
    font-weight: 400;
  }
  .brand__dot {
    display: block;
    margin: 0 auto;
    border-radius: 50%;
    background: var(--gold);
  }
  .brand--front { left: 110px; width: 230px; top: 140px; }
  .brand--front .brand__dot { width: 40px; height: 40px; margin-bottom: 22px; }
  .brand--front .brand__name { font-size: 26px; letter-spacing: 7px; }

  .divider {
    position: absolute;
    left: 355px;
    top: 128px;
    width: 1px;
    height: 142px;
    background: var(--rule);
  }

  .person {
    position: absolute;
    left: 384px;
    top: 126px;
  }
  .person__name {
    margin: 0;
    font-size: 21px;
    font-weight: 400;
    color: var(--gold);
  }
  .person__role {
    margin: 5px 0 0;
    font-size: 15.5px;
    color: #777;
  }

  .contacts {
    position: absolute;
    left: 384px;
    top: 206px;
    margin: 0;
    padding: 0;
    list-style: none;
    font-size: 16px;
    color: var(--ink);
  }
  .contacts li {
    display: flex;
    align-items: center;
    height: 21px;
  }
  .contacts svg {
    width: 12px;
    height: 12px;
    margin-right: 8px;
    fill: var(--gold);
    flex: none;
  }

  .brand--back { left: 0; width: 688px; top: 128px; }
  .brand--back .brand__dot { width: 56px; height: 56px; margin-bottom: 20px; }
  .brand--back .brand__name { font-size: 34px; letter-spacing: 9px; }

  .back-url {
    position: absolute;
    left: 0;
    width: 688px;
    top: 302px;
    text-align: center;
    font-size: 16px;
    letter-spacing: 1px;
    color: var(--ink);
  }
</style>
</head>
<body>
<main class="canvas">

  <section class="card card--front">
    <div class="brand brand--front">
      <span class="brand__dot"></span>
      <span class="brand__name">TALMORK</span>
    </div>

    <span class="divider"></span>

    <div class="person">
      <h1 class="person__name">Anders Vik Holmstad</h1>
      <p class="person__role">CEO &amp; Founder</p>
    </div>

    <ul class="contacts">
      <li>
        <svg viewBox="0 0 12 12" aria-hidden="true"><path d="M3 0h6a1 1 0 0 1 1 1v10a1 1 0 0 1-1 1H3a1 1 0 0 1-1-1V1a1 1 0 0 1 1-1zm.6 1.4v8.2h4.8V1.4z"/></svg>
        004791234567
      </li>
      <li>
        <svg viewBox="0 0 12 12" aria-hidden="true"><path d="M0 2.5h12v7H0zM1 3.3l5 3.4 5-3.4V3.2H1z"/></svg>
        talmork.llc@mailbox.com
      </li>
      <li>
        <svg viewBox="0 0 12 12" aria-hidden="true"><circle cx="6" cy="6" r="6"/></svg>
        www.talmork.llc
      </li>
    </ul>
  </section>

  <section class="card card--back">
    <div class="brand brand--back">
      <span class="brand__dot"></span>
      <span class="brand__name">TALMORK</span>
    </div>
    <p class="back-url">www.talmork.llc</p>
  </section>

</main>
</body>
</html>
```